Real Estate Business Card

On the front side I want to have my info, my brokerage info.
On the back side I want have my complany’s logo, website and Facebook link. I will provide all this once I select a design.

I would like to see Black background and gold text, Dark Blue and gold text and White and blue text designs

Font styles to use
Sans Serif
Script

```html
<!DOCTYPE html>
<html lang="en">
<head>
<meta charset="utf-8">
<title>Stoneway Realty – Business Card</title>
<link rel="stylesheet" href="https://fonts.googleapis.com/css2?family=Montserrat:wght@800&family=Oswald:wght@500&family=Work+Sans:wght@400&display=swap">
<style>
  :root {
    --backdrop: #1e1e1e;
    --card: #141414;
    --card-edge: #1b1b1b;
    --spot-gloss: #070707;
    --foil: #b9b9b9;
    --foil-soft: #8e8e8e;
    --divider: #3a3a3a;
    --badge: #f2f2f2;
  }
  html, body {
    margin: 0;
    width: 1200px;
    height: 900px;
    overflow: hidden;
    background: var(--backdrop);
  }
  .canvas {
    position: relative;
    width: 1200px;
    height: 900px;
  }
  .card {
    position: absolute;
    left: 280px;
    width: 640px;
    height: 366px;
    background: linear-gradient(135deg, var(--card) 0%, var(--card-edge) 60%, #242424 100%);
    box-shadow: 0 18px 40px rgba(0,0,0,0.55);
  }
  .card--front { top: 50px; }
  .card--back { top: 470px; }

  /* Front: brand mark */
  .brand {
    position: absolute;
    inset: 0;
    display: flex;
    align-items: center;
    justify-content: center;
    gap: 16px;
  }
  .brand__square {
    width: 34px;
    height: 34px;
    background: var(--foil);
  }
  .brand__name {
    font-family: 'Montserrat', sans-serif;
    font-weight: 800;
    font-size: 44px;
    letter-spacing: 1px;
    color: var(--foil);
  }

  /* Back: details */
  .identity {
    position: absolute;
    left: 70px;
    top: 110px;
    width: 250px;
    text-align: right;
  }
  .identity__name {
    font-family: 'Oswald', sans-serif;
    font-weight: 500;
    font-size: 40px;
    line-height: 1;
    color: var(--spot-gloss);
    text-shadow: 0 1px 0 #2c2c2c;
    text-transform: uppercase;
  }
  .identity__role {
    font-family: 'Work Sans', sans-serif;
    font-size: 16px;
    color: #2b2b2b;
    margin-top: 4px;
  }
  .divider {
    position: absolute;
    left: 338px;
    top: 108px;
    width: 2px;
    height: 60px;
    background: var(--divider);
  }
  .contact {
    position: absolute;
    left: 356px;
    top: 106px;
    margin: 0;
    padding: 0;
    list-style: none;
    font-family: 'Work Sans', sans-serif;
    font-size: 17px;
    color: var(--foil);
  }
  .contact li {
    display: flex;
    align-items: center;
    gap: 10px;
    height: 22px;
  }
  .contact svg {
    width: 12px;
    height: 12px;
    fill: none;
    stroke: var(--foil-soft);
    stroke-width: 1.6;
  }
  .address {
    position: absolute;
    left: 36px;
    top: 270px;
    font-family: 'Work Sans', sans-serif;
    font-size: 16px;
    line-height: 1.35;
    color: #0a0a0a;
    text-shadow: 0 1px 0 #2e2e2e;
  }
  .badge {
    position: absolute;
    top: 272px;
    background: var(--badge);
  }
  .badge--brokerage { left: 300px; width: 116px; height: 38px; }
  .badge--award { left: 440px; width: 98px; height: 38px; }
</style>
</head>
<body>
<main class="canvas">
  <section class="card card--front">
    <div class="brand">
      <span class="brand__square"></span>
      <span class="brand__name">STONEWAY REALTY</span>
    </div>
  </section>

  <section class="card card--back">
    <div class="identity">
      <div class="identity__name">Daniel Harper</div>
      <div class="identity__role">Director</div>
    </div>
    <div class="divider"></div>
    <ul class="contact">
      <li>
        <svg viewBox="0 0 12 12"><path d="M2 1.5l2 0 1 2.5-1.2 1a6 6 0 0 0 3.2 3.2l1-1.2 2.5 1v2a1 1 0 0 1-1 1A9 9 0 0 1 1 2.5a1 1 0 0 1 1-1z"/></svg>
        +1 555-014-2290
      </li>
      <li>
        <svg viewBox="0 0 12 12"><rect x="1" y="2.5" width="10" height="7"/><path d="M1 2.5l5 4 5-4"/></svg>
        hello@stonewayrealty.com
      </li>
      <li>
        <svg viewBox="0 0 12 12"><circle cx="6" cy="6" r="5"/><path d="M1 6h10M6 1c2.5 3 2.5 7 0 10M6 1c-2.5 3-2.5 7 0 10"/></svg>
        www.stonewayrealty.com
      </li>
    </ul>
    <div class="address">1180 Birch Lane #12<br>Fairview, Alberta T4X 3K1</div>
    <div class="badge badge--brokerage" role="img" aria-label="Brokerage badge"></div>
    <div class="badge badge--award" role="img" aria-label="Award badge"></div>
  </section>
</main>
</body>
</html>
```